Birchline Septic Solutions

Would like to see some single sided ones but would also like to see some double sided with one sided only being the logo. Owners name is Colin Vandro. Phone number is 555-214-0387
Services are pumping, inspections, installs, and repairs

Contact Information for Business Card

555-241-0387 Colin Vandro Alder Falls, OH

```html
<!DOCTYPE html>
<html lang="en">
<head>
<meta charset="utf-8">
<title>Birchline Septic Solutions – Business Card</title>
<link rel="stylesheet" href="https://fonts.googleapis.com/css2?family=Open+Sans:wght@400;600;700&display=swap">
<style>
  :root {
    --backdrop: #232323;
    --card: #1f1f22;
    --ink: #ffffff;
    --accent: #2bbbb3;
    --rule: #bdbdbd;
  }
  * { box-sizing: border-box; margin: 0; padding: 0; }
  html, body {
    width: 1200px; height: 779px; overflow: hidden;
    background: var(--backdrop);
    font-family: "Open Sans", Arial, sans-serif;
    color: var(--ink);
  }
  .stage {
    width: 1200px; height: 779px;
    display: flex; align-items: center; justify-content: center; gap: 40px;
  }
  .card {
    position: relative;
    width: 540px; height: 309px;
    background: var(--card);
    border-radius: 22px;
    box-shadow: 0 14px 30px rgba(0,0,0,.55);
  }
  /* Front: name only */
  .card--front { display: flex; align-items: center; justify-content: center; }
  .brand {
    display: flex; align-items: center; gap: 12px;
    font-weight: 700; color: var(--ink);
  }
  .brand__dot {
    width: 16px; height: 16px; border-radius: 50%;
    background: var(--accent); flex: none;
  }
  .card--front .brand__name { font-size: 30px; line-height: 1.15; width: 250px; }
  /* Back: details */
  .card--back .brand {
    position: absolute; left: 42px; top: 82px; gap: 10px;
  }
  .card--back .brand__dot { width: 12px; height: 12px; }
  .card--back .brand__name { font-size: 20px; line-height: 1.2; width: 170px; }
  .divider {
    position: absolute; left: 262px; top: 52px;
    width: 1px; height: 130px; background: var(--rule);
  }
  .contact { position: absolute; left: 292px; top: 64px; }
  .contact__name { font-size: 27px; font-weight: 700; line-height: 1.1; }
  .contact__first { color: var(--accent); }
  .contact__line { font-size: 15px; font-weight: 400; margin-top: 6px; display: flex; align-items: center; gap: 7px; }
  .contact__icon { width: 14px; height: 14px; flex: none; }
  .services { position: absolute; left: 0; right: 0; bottom: 40px; text-align: center; }
  .services__label {
    display: inline-block;
    background: var(--accent); color: var(--ink);
    font-size: 13px; font-weight: 600; letter-spacing: .5px;
    padding: 3px 22px; border-radius: 50%;
    margin-bottom: 10px;
  }
  .services__list {
    list-style: none; display: flex; justify-content: center; gap: 14px;
    font-size: 15px;
  }
  .services__item { display: flex; align-items: center; gap: 6px; }
  .services__item::before {
    content: ""; width: 9px; height: 9px; border-radius: 50%; background: var(--accent);
  }
</style>
</head>
<body>
<main class="stage">
  <section class="card card--front" aria-label="Card front">
    <div class="brand">
      <span class="brand__dot"></span>
      <span class="brand__name">Birchline Septic Solutions</span>
    </div>
  </section>

  <section class="card card--back" aria-label="Card back">
    <div class="brand">
      <span class="brand__dot"></span>
      <span class="brand__name">Birchline Septic Solutions</span>
    </div>
    <span class="divider"></span>
    <div class="contact">
      <p class="contact__name"><span class="contact__first">Colin</span> Vandro</p>
      <p class="contact__line">Alder Falls, OH</p>
      <p class="contact__line">
        <svg class="contact__icon" viewBox="0 0 24 24" aria-hidden="true">
          <path fill="var(--accent)" d="M6.6 10.8a15.1 15.1 0 0 0 6.6 6.6l2.2-2.2a1 1 0 0 1 1-.25 11.4 11.4 0 0 0 3.6.57 1 1 0 0 1 1 1V20a1 1 0 0 1-1 1A17 17 0 0 1 3 4a1 1 0 0 1 1-1h3.5a1 1 0 0 1 1 1c0 1.25.2 2.45.57 3.57a1 1 0 0 1-.25 1z"/>
        </svg>
        555-241-0387
      </p>
    </div>
    <div class="services">
      <span class="services__label">SERVICES</span>
      <ul class="services__list">
        <li class="services__item">Pumping</li>
        <li class="services__item">Inspections</li>
        <li class="services__item">Installs</li>
        <li class="services__item">And Repairs</li>
      </ul>
    </div>
  </section>
</main>
</body>
</html>
```